Business Card Design

My business is writing crime novels to entertain readers. I write legal thrillers and mysteries. I need a card for publishers, agents, other authors, and media.

Industry/Entity Type

Legal

Contact Information for Business Card

Paul Derrow
www.derrowfiction.example
pauljderrow@inkpost.example
0064 27 5190472

```html
<!DOCTYPE html>
<html lang="en">
<head>
<meta charset="utf-8">
<title>Paul Derrow – Business Card</title>
<link href="https://fonts.googleapis.com/css2?family=Gentium+Book+Plus&family=Open+Sans:wght@400;600&display=swap" rel="stylesheet">
<style>
  :root {
    --page: #e9e7e4;
    --card: #ffffff;
    --ink: #1c1c1c;
    --grey-text: #555555;
    --accent: #a4231f;
    --photo-light: #8a8a8a;
    --photo-dark: #5e5e5e;
  }
  html, body {
    margin: 0;
    width: 1200px;
    height: 873px;
    overflow: hidden;
    background: var(--page);
  }
  .business-card {
    position: absolute;
    left: 250px;
    top: 236px;
    width: 700px;
    height: 400px;
    background: var(--card);
    box-shadow: 0 10px 30px rgba(0,0,0,0.18);
    overflow: hidden;
  }
  .portrait-area {
    position: absolute;
    inset: 0;
    width: 700px;
    height: 400px;
  }
  .author-name {
    position: absolute;
    right: 40px;
    top: 48px;
    margin: 0;
    font-family: "Gentium Book Plus", Georgia, serif;
    font-weight: 400;
    font-size: 50px;
    line-height: 1;
    color: var(--ink);
  }
  .genre-band {
    position: absolute;
    right: 40px;
    top: 118px;
    width: 300px;
    padding: 8px 14px;
    box-sizing: border-box;
    background: var(--accent);
    color: var(--card);
    font-family: "Open Sans", Arial, sans-serif;
    font-size: 17px;
    letter-spacing: 1.5px;
    line-height: 1.3;
    text-transform: uppercase;
  }
  .contact-list {
    position: absolute;
    left: 380px;
    top: 218px;
    margin: 0;
    padding: 0;
    list-style: none;
    font-family: "Open Sans", Arial, sans-serif;
    font-size: 18px;
    color: var(--grey-text);
  }
  .contact-item {
    display: flex;
    align-items: center;
    gap: 12px;
    height: 34px;
  }
  .contact-icon {
    width: 20px;
    height: 20px;
    flex: none;
  }
</style>
</head>
<body>
  <div class="business-card">
    <svg class="portrait-area" viewBox="0 0 700 400" aria-hidden="false">
      <defs>
        <linearGradient id="portraitTone" x1="0" y1="0" x2="0" y2="1">
          <stop offset="0" stop-color="var(--photo-light)"/>
          <stop offset="1" stop-color="var(--photo-dark)"/>
        </linearGradient>
      </defs>
      <polygon points="0,0 350,0 270,400 0,400" fill="url(#portraitTone)" role="img" aria-label="Portrait photograph of the author against a grey studio background"/>
      <line class="divider-line" x1="350" y1="0" x2="270" y2="400" stroke="var(--accent)" stroke-width="6"/>
    </svg>

    <h1 class="author-name">Paul Derrow</h1>
    <div class="genre-band">Legal Thrillers<br>and Mysteries Writing</div>

    <ul class="contact-list">
      <li class="contact-item">
        <svg class="contact-icon" viewBox="0 0 20 20"><rect x="5" y="1" width="10" height="18" rx="2" fill="var(--accent)"/><rect x="7" y="4" width="6" height="9" fill="var(--card)"/></svg>
        <span>0064 27 5190472</span>
      </li>
      <li class="contact-item">
        <svg class="contact-icon" viewBox="0 0 20 20"><rect x="1" y="4" width="18" height="12" rx="1.5" fill="var(--accent)"/><polyline points="2,5 10,11 18,5" fill="none" stroke="var(--card)" stroke-width="1.5"/></svg>
        <span>pauljderrow@inkpost.example</span>
      </li>
      <li class="contact-item">
        <svg class="contact-icon" viewBox="0 0 20 20"><circle cx="10" cy="10" r="9" fill="var(--accent)"/><g fill="none" stroke="var(--card)" stroke-width="1.2"><ellipse cx="10" cy="10" rx="4" ry="9"/><line x1="1" y1="10" x2="19" y2="10"/><line x1="3" y1="5.5" x2="17" y2="5.5"/><line x1="3" y1="14.5" x2="17" y2="14.5"/></g></svg>
        <span>www.derrowfiction.example</span>
      </li>
    </ul>
  </div>
</body>
</html>
```